Business Card Design Project

Business Card
We are rebranding with a new logo
Industry/Entity Type
Business
Contact Information for Business Card
Dennis Morvale +61 487215963 dennis@quorv.com.au P.O. Box 872 Fernlow QLD 4309
Requirements
Must have
- Logo

```html
<!DOCTYPE html>
<html lang="en">
<head>
<meta charset="utf-8">
<title>Quorv International – Business Card</title>
<link href="https://fonts.googleapis.com/css2?family=Open+Sans:wght@400;600;700&display=swap" rel="stylesheet">
<style>
  :root {
    --backdrop: #1e1e1e;
    --card-white: #f7f7f6;
    --brand-blue: #1b8fc0;
    --brand-blue-deep: #13709a;
    --logo-blue: #1a78ad;
    --text-white: #ffffff;
  }
  html, body {
    margin: 0;
    padding: 0;
    width: 1200px;
    height: 915px;
    overflow: hidden;
    background: var(--backdrop);
    font-family: "Open Sans", Arial, sans-serif;
  }
  .canvas {
    position: relative;
    width: 1200px;
    height: 915px;
  }
  .card {
    position: absolute;
    left: 150px;
    top: 200px;
    width: 900px;
    height: 514px;
    background: var(--card-white);
    overflow: hidden;
  }
  .card__band {
    position: absolute;
    inset: 0;
    width: 900px;
    height: 514px;
  }
  .brand {
    position: absolute;
    left: 90px;
    top: 150px;
    color: var(--logo-blue);
    font-weight: 600;
    line-height: 1;
  }
  .brand__name {
    display: block;
    font-size: 92px;
    letter-spacing: -1px;
  }
  .brand__descriptor {
    display: block;
    margin-top: 14px;
    margin-left: 6px;
    font-size: 29px;
    letter-spacing: 5px;
  }
  .contact {
    position: absolute;
    right: 40px;
    top: 272px;
    text-align: right;
    color: var(--text-white);
  }
  .contact__name {
    margin: 0 0 8px;
    font-size: 22px;
    font-weight: 700;
    letter-spacing: 0.3px;
    text-transform: uppercase;
  }
  .contact__line {
    display: flex;
    justify-content: flex-end;
    align-items: center;
    gap: 10px;
    margin: 0;
    font-size: 18px;
    line-height: 28px;
  }
  .contact__icon {
    width: 17px;
    height: 17px;
    flex: none;
  }
</style>
</head>
<body>
<main class="canvas">
  <section class="card">
    <svg class="card__band" viewBox="0 0 900 514" aria-hidden="true">
      <path d="M0,458 C325,468 632,318 866,0 L900,0 L900,514 L0,514 Z" fill="var(--brand-blue-deep)"/>
      <path d="M0,470 C330,480 640,330 880,0 L900,0 L900,514 L0,514 Z" fill="var(--brand-blue)"/>
    </svg>

    <div class="brand">
      <span class="brand__name">Quorv</span>
      <span class="brand__descriptor">INTERNATIONAL</span>
    </div>

    <div class="contact">
      <p class="contact__name">Dennis Morvale</p>
      <p class="contact__line">+61 487215963
        <svg class="contact__icon" viewBox="0 0 20 20" aria-hidden="true"><path d="M2,7 Q10,1 18,7 L16,9 L13,7.5 L13,6 Q10,5 7,6 L7,7.5 L4,9 Z M5,10 L15,10 L17,17 L3,17 Z" fill="#fff"/></svg>
      </p>
      <p class="contact__line">dennis@quorv.com.au
        <svg class="contact__icon" viewBox="0 0 20 20" aria-hidden="true"><rect x="2" y="5" width="16" height="11" rx="1" fill="#fff"/><path d="M2.5,5.5 L10,11 L17.5,5.5" fill="none" stroke="var(--brand-blue)" stroke-width="1.4"/></svg>
      </p>
      <p class="contact__line">www.quorv.com.au
        <svg class="contact__icon" viewBox="0 0 20 20" aria-hidden="true"><circle cx="10" cy="10" r="8" fill="#fff"/><path d="M6,6 Q9,5 9,8 Q7,10 5,9 Z M11,11 Q14,10 15,13 Q13,16 11,15 Z" fill="var(--brand-blue)"/></svg>
      </p>
      <p class="contact__line">P.O. Box 872, Fernlow QLD 4309</p>
    </div>
  </section>
</main>
</body>
</html>
```